Book Cover for Lanterns Along the Quiet Threshold

I need a book cover for a 6 x 9 paperback titled Lanterns Along the Quiet Threshold Gathered from Research and Voices Dwelling in the Realm beyond Our Present Days. It has to do with consciousness, the mind, incarnation onto Earth, leaving Earth, and the life in the life after this life. I have an idea I'm providing with this description, but I am open to anything that would be striking and stimulating, whether with a book or not. I am the author, T. Morgan Wexley. I've added another background idea to see if anyone can do something with it and I've increased the budget.

```html
<!DOCTYPE html>
<html lang="en">
<head>
<meta charset="utf-8">
<title>Lanterns Along the Quiet Threshold — T. Morgan Wexley</title>
<link rel="stylesheet" href="https://fonts.googleapis.com/css2?family=Cinzel:wght@700;900&family=Libre+Baskerville:wght@400;700&display=swap">
<style>
  :root {
    --bg-deep: #1a0c06;
    --bg-warm: #3b1f12;
    --glow-core: #fff8e2;
    --glow-mid: #f0c777;
    --glow-amber: #c6853a;
    --glow-edge: #6e3c17;
    --gold-light: #f9e3a6;
    --gold: #dba54c;
    --gold-dark: #a06b25;
    --ornament: #a8642e;
    --cream: #f3e6cc;
  }
  * { margin: 0; padding: 0; box-sizing: border-box; }
  html, body {
    width: 800px; height: 1200px; overflow: hidden;
    background: var(--bg-deep);
  }
  .cover {
    position: relative;
    width: 800px; height: 1200px;
    overflow: hidden;
    background:
      radial-gradient(ellipse 75% 40% at 50% 22%, rgba(95,52,26,.6), transparent 72%),
      linear-gradient(180deg, var(--bg-warm) 0%, #2a150b 50%, var(--bg-deep) 100%);
    text-align: center;
  }
  .radiant-book {
    position: absolute;
    left: 0; top: 480px; width: 800px; height: 640px;
    background:
      radial-gradient(ellipse 22% 18% at 50% 52%, var(--glow-core) 0%, rgba(255,240,200,.9) 35%, transparent 100%),
      radial-gradient(ellipse 44% 30% at 50% 58%, rgba(240,199,119,.85) 0%, rgba(198,133,58,.55) 45%, transparent 85%),
      radial-gradient(ellipse 48% 10% at 50% 82%, rgba(250,232,190,.75) 0%, rgba(198,133,58,.35) 60%, transparent 100%),
      radial-gradient(ellipse 70% 55% at 50% 50%, rgba(160,95,40,.5) 0%, rgba(110,60,23,.25) 55%, transparent 85%);
  }
  .ornament {
    position: absolute;
    left: 50%; transform: translateX(-50%);
    background: radial-gradient(ellipse 50% 50% at 50% 50%, #c98045 0%, var(--ornament) 45%, transparent 75%);
    opacity: .7;
  }
  .ornament--top { top: 104px; width: 250px; height: 86px; }
  .ornament--bottom { top: 462px; width: 250px; height: 80px; }
  .rule { position: absolute; left: 110px; }
  .rule--top { top: 196px; }
  .rule--bottom { top: 454px; }
  .title {
    position: absolute; left: 0; right: 0; top: 218px;
    font-family: "Cinzel", serif;
    line-height: 1;
  }
  .title span {
    display: block;
    background: linear-gradient(180deg, var(--gold-light) 0%, var(--gold) 55%, var(--gold-dark) 100%);
    -webkit-background-clip: text; background-clip: text;
    color: transparent;
  }
  .title__lead, .title__tail { font-weight: 900; font-size: 60px; letter-spacing: 1px; }
  .title__middle {
    margin-top: 4px;
    font-family: "Libre Baskerville", serif;
    font-weight: 700;
    font-size: 40px;
    line-height: 46px;
  }
  .title__tail { margin-top: 4px; }
  .subtitle {
    position: absolute; left: 0; right: 0; top: 392px;
    font-family: "Libre Baskerville", serif;
    font-weight: 400;
    font-size: 22px;
    line-height: 28px;
    color: var(--cream);
  }
  .author {
    position: absolute; left: 0; right: 0; top: 1060px;
    font-family: "Libre Baskerville", serif;
    font-weight: 700;
    font-size: 44px;
    color: var(--cream);
  }
</style>
</head>
<body>
<main class="cover">
  <div class="radiant-book" role="img" aria-label="Open book with fanned pages, golden light and sparkles streaming upward from it"></div>

  <div class="ornament ornament--top" role="img" aria-label="Copper scroll flourish"></div>
  <svg class="rule rule--top" width="580" height="4" viewBox="0 0 580 4" aria-hidden="true">
    <line x1="0" y1="2" x2="580" y2="2" stroke="#a8642e" stroke-width="1.5"/>
  </svg>

  <h1 class="title">
    <span class="title__lead">Lanterns Along</span>
    <span class="title__middle">the Quiet</span>
    <span class="title__tail">Threshold</span>
  </h1>

  <p class="subtitle">Gathered from Research and Voices Dwelling<br>in the Realm beyond Our Present Days</p>

  <svg class="rule rule--bottom" width="580" height="4" viewBox="0 0 580 4" aria-hidden="true">
    <line x1="0" y1="2" x2="580" y2="2" stroke="#a8642e" stroke-width="1.5"/>
  </svg>
  <div class="ornament ornament--bottom" role="img" aria-label="Copper scroll flourish"></div>

  <p class="author">T. Morgan Wexley</p>
</main>
</body>
</html>
```